BRVKT Pharma Brochure

Create a BRVKT brochure that targets the pharmaceutical industry using our literature along with vendors literature for the cleanest look.

Bullet points will be

Services:
24/7 Emergency Service
Break Fix
PM Programs
Design Build
In House Electricians and Millwrights
Electrical Trouble Shooting

Products:
ISO Rates Products
High Speed Doors
Sliding Doors
Swinging Doors
Low Energy Closers
Overhead Doors
Loading Dock Equipment
Modular Offices and Rooms
Osha 10 and 30 Compliant

https://www.plimorentryworks.example/en/products/automatic-pedestrian-doors/hermetic-doors/plimor-garna-kq-zt

```html
<!DOCTYPE html>
<html lang="en">
<head>
<meta charset="utf-8">
<title>BRVKT Pharma Brochure</title>
<link href="https://fonts.googleapis.com/css2?family=Montserrat:wght@400;700;800&family=Oswald:wght@500&display=swap" rel="stylesheet">
<style>
:root{
  --stage:#e4e4e8;
  --paper:#ffffff;
  --brand-red:#c4222c;
  --footer-red:#c8343c;
  --navy:#3a3a86;
  --band-navy:#34326f;
  --ink:#050505;
  --photo-light:#d8eef8;
  --photo-mid:#8fbfd8;
  --photo-dark:#3d6782;
  --tile-light:#eef0f2;
  --tile-dark:#6b7075;
}
*{box-sizing:border-box;margin:0;padding:0}
html,body{width:1200px;height:900px;overflow:hidden}
body{background:var(--stage);font-family:"Montserrat",Arial,sans-serif;position:relative}
.page{position:absolute;top:121px;width:470px;height:657px;background:var(--paper);overflow:hidden;box-shadow:0 6px 18px rgba(0,0,0,.18)}
.page--cover{left:110px}
.page--back{left:620px}

/* cover */
.cover-photo{position:absolute;left:0;top:100px;width:470px;height:557px;
  background:
    linear-gradient(180deg,#fff 0%,rgba(255,255,255,.6) 12%,rgba(255,255,255,0) 30%),
    radial-gradient(ellipse 40% 55% at 50% 45%,var(--photo-light) 0%,rgba(216,238,248,0) 100%),
    linear-gradient(90deg,var(--photo-dark) 0%,var(--photo-mid) 25%,var(--photo-light) 50%,var(--photo-mid) 75%,var(--photo-dark) 100%);}
.brand-mark{position:absolute;left:34px;top:26px;font-weight:800;font-size:68px;line-height:1;color:var(--brand-red);letter-spacing:1px}
.brand-name{position:absolute;left:35px;top:96px;font-size:16.5px;color:var(--navy);letter-spacing:.3px;text-transform:uppercase;white-space:nowrap}

/* back */
.section-band{position:absolute;left:4px;width:460px;height:33px;
  background:linear-gradient(90deg,var(--band-navy) 0%,#5a5890 45%,rgba(90,88,144,.35) 80%,rgba(255,255,255,0) 100%);
  color:#fff;font-weight:800;font-size:18px;letter-spacing:5px;line-height:33px;padding-left:26px}
.section-band--services{top:40px}
.section-band--products{top:246px}
.service{position:absolute;display:flex;align-items:center;gap:10px;color:var(--navy);font-size:12.5px;line-height:1.2;text-transform:uppercase;white-space:nowrap}
.service::before{content:"";flex:none;width:34px;height:34px;border-radius:50%;background:var(--ink)}
.service span{display:block}
.product{position:absolute;width:90px;text-align:center}
.product-photo{display:block;width:88px;height:100px;margin:0 auto;border:2px solid var(--brand-red);border-radius:10px;
  background:linear-gradient(180deg,var(--tile-dark) 0%,#a9aeb2 35%,var(--tile-light) 80%,#fff 100%)}
.product-name{width:110px;margin:8px 0 0 -10px;font-family:"Oswald",Arial,sans-serif;font-weight:500;font-size:9px;letter-spacing:.5px;color:var(--navy);text-transform:uppercase;line-height:1.45;white-space:nowrap}
.page-footer{position:absolute;left:4px;right:4px;bottom:0;height:76px;background:var(--footer-red);color:#fff;font-size:10.5px}
.footer-col{position:absolute;top:18px;display:flex;flex-direction:column;gap:9px}
.footer-line{display:flex;align-items:center;gap:5px;white-space:nowrap}
.social-dot{width:11px;height:11px;background:#fff;border-radius:2px}
.divider{position:absolute;top:18px;width:2px;height:38px;background:#fff}
.footer-brand{position:absolute;left:312px;top:22px;width:140px;font-weight:700;font-size:12px;line-height:1.25;text-align:center}
</style>
</head>
<body>
<section class="page page--cover">
  <div class="cover-photo" role="img" aria-label="Photo of a bright clean pharmaceutical corridor with stainless steel doors and a potted plant"></div>
  <h1 class="brand-mark">BRVKT</h1>
  <p class="brand-name">Bryvekta Door &amp; Dock Works</p>
</section>

<section class="page page--back">
  <h2 class="section-band section-band--services">SERVICES</h2>
  <div class="service" style="left:30px;top:88px"><span>24/7 Emergency<br>Service</span></div>
  <div class="service" style="left:30px;top:141px"><span>Break Fix</span></div>
  <div class="service" style="left:30px;top:193px"><span>PM Programs</span></div>
  <div class="service" style="left:244px;top:88px"><span>Design Build</span></div>
  <div class="service" style="left:244px;top:141px"><span>In House Electricians<br>&nbsp;and Millwrights</span></div>
  <div class="service" style="left:244px;top:193px"><span>Electrical Trouble<br>&nbsp;Shooting</span></div>

  <h2 class="section-band section-band--products">PRODUCTS</h2>
  <div class="product" style="left:24px;top:304px"><span class="product-photo" role="img" aria-label="Photo of an ISO rated door"></span><p class="product-name">ISO Rates Products</p></div>
  <div class="product" style="left:133px;top:304px"><span class="product-photo" role="img" aria-label="Photo of a high speed door"></span><p class="product-name">High Speed Doors</p></div>
  <div class="product" style="left:242px;top:304px"><span class="product-photo" role="img" aria-label="Photo of a sliding door"></span><p class="product-name">Sliding Doors</p></div>
  <div class="product" style="left:351px;top:304px"><span class="product-photo" role="img" aria-label="Photo of a swinging door"></span><p class="product-name">Swinging Doors</p></div>
  <div class="product" style="left:24px;top:436px"><span class="product-photo" role="img" aria-label="Photo of a modular office door"></span><p class="product-name">Modular Offices<br>and Rooms</p></div>
  <div class="product" style="left:133px;top:436px"><span class="product-photo" role="img" aria-label="Photo of an overhead door"></span><p class="product-name">Overhead Doors</p></div>
  <div class="product" style="left:242px;top:436px"><span class="product-photo" role="img" aria-label="Photo of loading dock equipment"></span><p class="product-name">Loading Dock<br>Equipment</p></div>
  <div class="product" style="left:351px;top:436px"><span class="product-photo" role="img" aria-label="Photo of a door with a low energy closer"></span><p class="product-name">Low Energy Closers</p></div>

  <footer class="page-footer">
    <div class="footer-col" style="left:24px">
      <div class="footer-line"><span class="social-dot"></span>yoursite.com</div>
      <div class="footer-line"><span class="social-dot"></span>yoursite.com</div>
    </div>
    <span class="divider" style="left:142px"></span>
    <div class="footer-col" style="left:162px">
      <div class="footer-line">
        <svg width="9" height="12" viewBox="0 0 9 12"><path d="M4.5 0a4.5 4.5 0 0 0-4.5 4.5C0 8 4.5 12 4.5 12S9 8 9 4.5A4.5 4.5 0 0 0 4.5 0zm0 6.3a1.8 1.8 0 1 1 0-3.6 1.8 1.8 0 0 1 0 3.6z" fill="#fff"/></svg>
        Address line. 12345</div>
      <div class="footer-line">
        <svg width="11" height="11" viewBox="0 0 24 24"><path d="M6.6 10.8a15.1 15.1 0 0 0 6.6 6.6l2.2-2.2c.3-.3.7-.4 1-.2 1.1.4 2.3.6 3.6.6.6 0 1 .4 1 1V20c0 .6-.4 1-1 1A17 17 0 0 1 3 4c0-.6.4-1 1-1h3.5c.6 0 1 .4 1 1 0 1.3.2 2.5.6 3.6.1.3 0 .7-.2 1z" fill="#fff"/></svg>
        123-000-456(123)</div>
    </div>
    <span class="divider" style="left:298px"></span>
    <p class="footer-brand">Bryvekta Door &amp; Dock Works</p>
  </footer>
</section>
</body>
</html>
```